Building company buisness cards

We are looking for a sharp modern new look for our business cards.
We are a New Zealand based company that specialises in house and land packages.
We have attached a photo of the current logo and would like to see if it can be improved somehow if needed.
We are open to any colours but we have chosen green at this stage.
Feel free to change the font and make the logo smarter looking.
Play with the colours and see what looks best.

We want a card that looks so good know one will want to throw it away!

Target Market(s)

Home buyers

Industry/Entity Type

Building

Contact Information for Business Card

Derek Tolvane
0217394062
dtolvane@quillmarkhomesteads.co.nz
quillmarkhomesteads.co.nz

Font styles to use
Serif
Sans Serif

Colors

Designer to choose colors to be used in the design.

Requirements
Must have
• Logo and company name on one side, details on the other side
Nice to have
• Color codes for the original green are HEX #4a8028, RGB(74,128,40), CMYK(42,0,69,50)
• Round corners, Raised and/or spot UV

```html
<!DOCTYPE html>
<html lang="en">
<head>
<meta charset="utf-8">
<title>Quillmark Homesteads — Business Cards</title>
<link rel="stylesheet" href="https://fonts.googleapis.com/css2?family=Nunito:wght@900&family=Arimo:wght@400;700&family=Open+Sans:wght@400&display=swap">
<style>
  :root {
    --brand-green: #4a8028;
    --ink: #000000;
    --paper: #ffffff;
    --silver: #8c8c8f;
    --backdrop: #cbcccd;
  }
  * { box-sizing: border-box; margin: 0; padding: 0; }
  html, body { width: 1200px; height: 940px; overflow: hidden; }
  body { background: var(--backdrop); position: relative; }

  .card {
    position: absolute;
    width: 637px;
    height: 364px;
    border-radius: 24px;
    overflow: hidden;
    box-shadow: 0 3px 6px rgba(0,0,0,0.25);
  }
  .card--front { left: 431px; top: 90px; background: var(--brand-green); }
  .card--back  { left: 165px; top: 511px; background: var(--brand-green); border-radius: 36px; }

  .card__art { position: absolute; inset: 0; width: 100%; height: 100%; }

  .company-name {
    position: absolute;
    font-family: "Nunito", sans-serif;
    font-weight: 900;
    text-align: center;
    line-height: 1;
    letter-spacing: -0.3px;
  }
  .company-name span { display: block; }
  .card--front .company-name { left: 0; width: 350px; top: 102px; color: var(--brand-green); }
  .card--front .company-name .line-1 { font-size: 22px; }
  .card--front .company-name .line-2 { font-size: 30px; margin-top: 2px; }
  .card--back .company-name { left: 0; width: 636px; top: 152px; color: var(--paper); }
  .card--back .company-name .line-1 { font-size: 32px; }
  .card--back .company-name .line-2 { font-size: 42px; margin-top: 2px; }

  .rule { position: absolute; height: 1.5px; }
  .card--front .rule { left: 110px; top: 175px; width: 111px; background: var(--brand-green); }
  .card--back .rule { left: 231px; top: 255px; width: 150px; background: var(--paper); height: 2px; }

  .holder { position: absolute; right: 30px; top: 24px; text-align: right; font-family: "Arimo", sans-serif; font-weight: 700; }
  .holder__name { color: var(--brand-green); font-size: 23px; line-height: 1.2; }
  .holder__title { color: var(--paper); font-size: 20px; line-height: 1.25; }

  .contacts { position: absolute; right: 29px; top: 267px; list-style: none; font-family: "Open Sans", sans-serif; color: var(--paper); font-size: 15px; letter-spacing: -0.4px; }
  .contacts li { display: flex; justify-content: flex-end; align-items: center; height: 27px; }
  .contacts svg { width: 14px; height: 14px; margin-left: 9px; flex: none; }

  .back-url {
    position: absolute; left: 0; width: 636px; top: 320px; text-align: center;
    font-family: "Open Sans", sans-serif; color: var(--paper); font-size: 16px; letter-spacing: 2.2px;
  }
</style>
</head>
<body>

<section class="card card--front" aria-label="Card front">
  <svg class="card__art" viewBox="0 0 1051 600" preserveAspectRatio="none" aria-hidden="true">
    <path d="M0 275 C120 470 420 500 660 420 S980 290 1051 318 L1051 0 L600 0 Z" fill="var(--ink)"/>
    <path d="M0 300 C140 470 430 470 660 410 S960 300 1051 330" fill="none" stroke="var(--silver)" stroke-width="4"/>
    <path d="M0 310 C150 480 440 480 670 418 S970 312 1051 345" fill="none" stroke="var(--brand-green)" stroke-width="10"/>
    <path d="M0 330 C160 490 450 475 680 420 S980 330 1051 355" fill="none" stroke="var(--silver)" stroke-width="4"/>
    <path d="M0 340 C170 500 460 480 690 425 S990 336 1051 363" fill="none" stroke="var(--paper)" stroke-width="4"/>
    <ellipse cx="290" cy="145" rx="362" ry="278" fill="var(--silver)"/>
    <ellipse cx="290" cy="145" rx="358" ry="275" fill="var(--brand-green)"/>
    <ellipse cx="288" cy="140" rx="346" ry="266" fill="var(--paper)"/>
    <ellipse cx="288" cy="138" rx="336" ry="260" fill="none" stroke="var(--silver)" stroke-width="3"/>
  </svg>

  <h1 class="company-name"><span class="line-1">quillmark</span><span class="line-2">homesteads.</span></h1>
  <div class="rule"></div>

  <div class="holder">
    <p class="holder__name">Derek Tolvane</p>
    <p class="holder__title">Title</p>
  </div>

  <ul class="contacts">
    <li>0217394062
      <svg viewBox="0 0 16 16" aria-hidden="true"><circle cx="8" cy="8" r="7" fill="none" stroke="currentColor" stroke-width="1.3"/><path d="M6 4.5c-1 1-1 3 .8 5s3.8 2.3 4.7 1.4l-1.2-1.3-1 .6c-.8-.4-1.7-1.4-2-2.2l.6-1z" fill="currentColor"/></svg>
    </li>
    <li>dtolvane@quillmarkhomesteads.co.nz
      <svg viewBox="0 0 16 16" aria-hidden="true"><path d="M1 6l7-4 7 4v8H1z" fill="currentColor"/><path d="M1 6l7 5 7-5" fill="none" stroke="var(--brand-green)" stroke-width="1.2"/></svg>
    </li>
    <li>www.quillmarkhomesteads.co.nz
      <svg viewBox="0 0 16 16" aria-hidden="true"><g fill="none" stroke="currentColor" stroke-width="1.1"><circle cx="8" cy="8" r="7"/><ellipse cx="8" cy="8" rx="3" ry="7"/><path d="M1 8h14M2.5 4.5h11M2.5 11.5h11"/></g></svg>
    </li>
  </ul>
</section>

<section class="card card--back" aria-label="Card back">
  <h2 class="company-name"><span class="line-1">quillmark</span><span class="line-2">homesteads.</span></h2>
  <div class="rule"></div>
  <p class="back-url">www.quillmarkhomesteads.co.nz</p>
</section>

</body>
</html>
```